Carpet cleaning company focused on high quality needs business cards

We are a growing company that just merged with another company and need to design a new business card. We do both residential as well as commercial cleaning. We do carpet, tile & grout, upholstery, hard floors, and stain & pet odor removal. We treat our customers like family and strive to achieve outstanding results with every job.

```html
<!DOCTYPE html>
<html lang="en">
<head>
<meta charset="utf-8">
<title>Harbor Lane Floorcare – Business Card</title>
<link href="https://fonts.googleapis.com/css2?family=Open+Sans:wght@400;700;800&display=swap" rel="stylesheet">
<style>
  :root {
    --bg: #232323;
    --card-white: #ffffff;
    --brand-red: #ec4a40;
    --accent-orange: #f05a28;
    --accent-blue: #2aa3e0;
    --band-blue: #0a84c6;
    --ink: #111111;
    --text: #222222;
  }
  * { box-sizing: border-box; margin: 0; padding: 0; }
  html, body { width: 1200px; height: 780px; overflow: hidden; }
  body {
    background: var(--bg);
    font-family: "Open Sans", Arial, sans-serif;
    position: relative;
  }
  .card {
    position: absolute;
    width: 600px;
    height: 343px;
    left: 300px;
    overflow: hidden;
  }
  .card--front { top: 24px; background: var(--card-white); }
  .card--back { top: 411px; background: var(--brand-red); }

  /* Front */
  .front-logo {
    position: absolute;
    left: 48px; top: 116px;
    display: flex; align-items: center; gap: 16px;
  }
  .logo-square {
    width: 58px; height: 58px;
    background: var(--brand-red);
    flex: none;
  }
  .logo-name {
    font-weight: 800;
    color: var(--ink);
    line-height: 1.1;
    font-size: 24px;
  }
  .divider {
    position: absolute;
    left: 300px; top: 48px;
    width: 1px; height: 180px;
    background: var(--ink);
  }
  .details {
    position: absolute;
    left: 330px; top: 46px;
  }
  .person-name { font-size: 30px; font-weight: 700; line-height: 1.1; }
  .person-name .first { color: var(--accent-orange); }
  .person-name .last { color: var(--accent-blue); }
  .person-title { font-size: 14px; color: var(--text); margin-top: 2px; }
  .contact-list { list-style: none; margin-top: 16px; }
  .contact-list li {
    display: flex; align-items: center; gap: 8px;
    font-size: 14px; color: var(--text); line-height: 1.45;
  }
  .contact-icon { width: 13px; height: 13px; flex: none; }

  .address-band {
    position: absolute;
    left: 0; bottom: 34px;
    width: 548px; height: 34px;
    background: var(--brand-red);
    color: #fff;
    font-size: 15px;
    display: flex; align-items: center;
    padding-left: 36px;
  }
  .band-mark {
    position: absolute;
    right: 64px; bottom: 38px;
    width: 26px; height: 26px;
    background: var(--card-white);
  }
  .band-blue {
    position: absolute;
    right: 0; bottom: 34px;
    width: 52px; height: 34px;
    background: var(--band-blue);
  }

  /* Back */
  .back-logo {
    position: absolute;
    inset: 0;
    display: flex; align-items: center; justify-content: center; gap: 28px;
  }
  .back-logo .logo-square { width: 110px; height: 110px; background: var(--card-white); }
  .back-logo .logo-name { font-size: 42px; }
</style>
</head>
<body>

<section class="card card--front" aria-label="Business card front">
  <div class="front-logo">
    <span class="logo-square" aria-hidden="true"></span>
    <p class="logo-name">Harbor Lane<br>Floorcare</p>
  </div>

  <div class="divider" aria-hidden="true"></div>

  <div class="details">
    <h1 class="person-name"><span class="first">Marta</span> <span class="last">Velinska</span></h1>
    <p class="person-title">Managing Director</p>
    <ul class="contact-list">
      <li>
        <svg class="contact-icon" viewBox="0 0 16 16" aria-hidden="true"><circle cx="8" cy="8" r="8" fill="#f05a28"/><path d="M5 4.5c.6-.4 1.2 0 1.4.6l.4 1c.1.4 0 .7-.3.9l-.4.3c.4.9 1.1 1.6 2 2l.3-.4c.2-.3.6-.4.9-.3l1 .4c.6.2 1 .8.6 1.4-.5.7-1.2 1-2 .8C6.7 10.7 5.3 9.3 4.8 7.1c-.2-.8.1-1.9.2-2.6z" fill="#fff"/></svg>
        (555) 014-2290
      </li>
      <li>
        <svg class="contact-icon" viewBox="0 0 16 16" aria-hidden="true"><circle cx="8" cy="8" r="8" fill="#f05a28"/><rect x="4" y="5" width="8" height="6" fill="none" stroke="#fff" stroke-width="1.2"/><path d="M4 5l4 3.2L12 5" fill="none" stroke="#fff" stroke-width="1.2"/></svg>
        hello@harborlane.com
      </li>
      <li>
        <svg class="contact-icon" viewBox="0 0 16 16" aria-hidden="true"><circle cx="8" cy="8" r="8" fill="#f05a28"/><circle cx="8" cy="8" r="4.5" fill="none" stroke="#fff" stroke-width="1.1"/><path d="M3.5 8h9M8 3.5c-2 2.5-2 6.5 0 9M8 3.5c2 2.5 2 6.5 0 9" fill="none" stroke="#fff" stroke-width="1"/></svg>
        www.harborlane.com
      </li>
    </ul>
  </div>

  <div class="address-band">418 Maple Grove Rd. Suite 120 Arlington, TX 76010</div>
  <div class="band-mark" aria-hidden="true"></div>
  <div class="band-blue" aria-hidden="true"></div>
</section>

<section class="card card--back" aria-label="Business card back">
  <div class="back-logo">
    <span class="logo-square" aria-hidden="true"></span>
    <p class="logo-name">Harbor Lane<br>Floorcare</p>
  </div>
</section>

</body>
</html>
```